Meridale Bed Company Needs Business Card

Looking for a very nice looking business card. Creative but not extravagant. We sell beds and pillows across the U.S. and need something professional but catchy. I have attached the logo.

Name : Devin Holt
Title : President
Phone : (800) 471-2960
Email: sleep@quilmora.com
Website: www.quilmora.com

Can be single-sided or double-sided
horizontal or vertical

Can use Blues/Greys

Target Market(s)

Mass Market

Industry/Entity Type

Retail

Contact Information for Business Card

Name : Devin Holt
Title : President
Phone : (800) 471-2960
Email: sleep@quilmora.com
Website: www.quilmora.com

Requirements
Must have
• Clean, Modern, Smooth
• Can use Blues/Greys
• On the other side without the information - have something simple like www.quilmora.com or our logo
Nice to have
• Surprise me
Should not have
• Nothing crazy, nothing cluttered

```html
<!DOCTYPE html>
<html lang="en">
<head>
<meta charset="utf-8">
<title>Quilmora Business Card</title>
<link href="https://fonts.googleapis.com/css2?family=Quicksand:wght@400;500;700&display=swap" rel="stylesheet">
<style>
  :root {
    --brand-blue: #2ea3d7;
    --grey-light: #aeb0b3;
    --grey-dark: #9c9ea1;
    --card-back: #b4b6b9;
    --ink: #4a4a4a;
    --paper: #ffffff;
    --page: #eeeeee;
  }
  * { margin: 0; padding: 0; box-sizing: border-box; }
  html, body {
    width: 1200px;
    height: 800px;
    overflow: hidden;
    background: var(--page);
    font-family: "Quicksand", sans-serif;
  }
  .sheet {
    width: 1200px;
    height: 800px;
    display: flex;
    flex-direction: column;
    align-items: center;
    justify-content: center;
    gap: 40px;
  }
  .card {
    position: relative;
    width: 620px;
    height: 354px;
    background: var(--paper);
    box-shadow: 0 6px 18px rgba(0,0,0,0.12);
    overflow: hidden;
  }
  .card-shapes {
    position: absolute;
    inset: 0;
    width: 100%;
    height: 100%;
  }

  /* Company name set in the card's text font */
  .company-name {
    font-weight: 700;
    letter-spacing: 0;
    line-height: 1;
  }

  /* Back */
  .card--back { background: var(--card-back); display: flex; align-items: center; justify-content: center; }
  .card--back .company-name { font-size: 60px; color: var(--paper); }

  /* Front */
  .card--front .company-name {
    position: absolute;
    left: 30px;
    top: 132px;
    font-size: 46px;
    color: var(--brand-blue);
  }
  .holder {
    position: absolute;
    right: 32px;
    top: 34px;
    text-align: center;
  }
  .holder-name {
    display: flex;
    align-items: center;
    gap: 6px;
    color: var(--brand-blue);
    font-weight: 700;
    font-size: 19px;
  }
  .holder-icon {
    width: 22px;
    height: 22px;
    background: var(--grey-dark);
    border-radius: 3px;
    display: flex;
    align-items: center;
    justify-content: center;
  }
  .holder-title {
    color: var(--ink);
    font-size: 13px;
    font-weight: 500;
    letter-spacing: 1px;
    margin-right: 24px;
  }
  .address {
    position: absolute;
    left: 28px;
    top: 290px;
    color: var(--paper);
    font-size: 12.5px;
    font-weight: 500;
    line-height: 1.25;
  }
  .address span { display: block; padding-left: 34px; }
  .contacts {
    position: absolute;
    right: 20px;
    top: 246px;
    list-style: none;
    color: var(--paper);
    font-size: 14px;
    font-weight: 500;
    letter-spacing: 0.5px;
  }
  .contacts li {
    display: flex;
    align-items: center;
    justify-content: flex-end;
    gap: 7px;
    height: 20px;
  }
  .contact-icon {
    width: 13px;
    height: 13px;
    background: var(--paper);
    border-radius: 2px;
    display: flex;
    align-items: center;
    justify-content: center;
  }
</style>
</head>
<body>
<main class="sheet">

  <section class="card card--back" aria-label="Card back">
    <span class="company-name">Quilmora</span>
  </section>

  <section class="card card--front" aria-label="Card front">
    <svg class="card-shapes" viewBox="0 0 620 354" aria-hidden="true">
      <polygon points="0,0 620,0 620,9 262,9 250,24 0,24" fill="var(--brand-blue)"/>
      <polygon points="266,13 612,13 612,22 259,22" fill="var(--grey-light)"/>
      <polygon points="0,252 290,252 282,270 0,270" fill="var(--grey-light)"/>
      <polygon points="0,274 280,274 244,354 0,354" fill="var(--grey-dark)"/>
      <polygon points="316,224 620,224 620,354 258,354" fill="var(--brand-blue)"/>
    </svg>

    <div class="holder">
      <div class="holder-name">
        Devin Holt
        <span class="holder-icon">
          <svg width="14" height="16" viewBox="0 0 14 16" aria-hidden="true">
            <circle cx="7" cy="4.5" r="3.5" fill="#fff"/>
            <path d="M0 16 C0 10 3 9 7 9 C11 9 14 10 14 16 Z" fill="#fff"/>
          </svg>
        </span>
      </div>
      <div class="holder-title">President</div>
    </div>

    <span class="company-name">Quilmora</span>

    <p class="address">Address line 1 , Address Line 2,<span>Address Line 3</span></p>

    <ul class="contacts">
      <li>(800) 471-2960
        <span class="contact-icon">
          <svg width="9" height="9" viewBox="0 0 10 10" aria-hidden="true"><path d="M2 0.5 L4 2.8 L3 4 C3.7 5.5 4.6 6.4 6 7 L7.2 6 L9.5 8 L8.3 9.5 C4.5 9.3 0.7 5.5 0.5 1.7 Z" fill="var(--brand-blue)"/></svg>
        </span>
      </li>
      <li>sleep@quilmora.com
        <span class="contact-icon">
          <svg width="9" height="7" viewBox="0 0 10 8" aria-hidden="true"><rect x="0.5" y="0.5" width="9" height="7" fill="none" stroke="var(--brand-blue)"/><path d="M0.5 0.5 L5 4.5 L9.5 0.5" fill="none" stroke="var(--brand-blue)"/></svg>
        </span>
      </li>
      <li>www.quilmora.com
        <span class="contact-icon">
          <svg width="9" height="9" viewBox="0 0 10 10" aria-hidden="true"><circle cx="5" cy="5" r="4.3" fill="none" stroke="var(--brand-blue)"/><ellipse cx="5" cy="5" rx="1.8" ry="4.3" fill="none" stroke="var(--brand-blue)"/><path d="M0.7 5 H9.3" stroke="var(--brand-blue)"/></svg>
        </span>
      </li>
    </ul>
  </section>

</main>
</body>
</html>
```